Bookcover: Ways to Turn Into a Bold Pathfinder

I am publishing a super-low-cost innovation book for €4,99 on Quillmere Open Press to help everyone become a great innovator: young ambitious people without college education nor a big budget. Do you want to help me?

Brief:
Design a book cover 1600 x 2560 pixels for QOP.
Main title: Ways to Turn Into a Bold Pathfinder
Sub title: mindset - insights - skills & tools
Author: Joost ter Brakel
Design: captive, and appealing to everyone
Target Group: young ambitious people without college education

For quillmere please format the height/width ratio of 1.6:1

```html
<!DOCTYPE html>
<html lang="en">
<head>
<meta charset="utf-8">
<title>Ways to Turn Into a Bold Pathfinder — Book Cover</title>
<link href="https://fonts.googleapis.com/css2?family=Poppins:wght@600;700&family=Roboto:wght@700&display=swap" rel="stylesheet">
<style>
  :root {
    --stage: #777777;
    --cover-top: #efbd4a;
    --cover-bottom: #e6ad3c;
    --glow-outer: rgba(255, 236, 180, 0.55);
    --glow-inner: rgba(255, 244, 210, 0.55);
    --ink: #2d2925;
    --accent: #8b2d45;
    --band: #333231;
    --band-text: #ececec;
    --icon-ink: #2a2622;
  }
  * { margin: 0; padding: 0; box-sizing: border-box; }
  html, body {
    width: 1200px; height: 1200px; overflow: hidden;
    background: var(--stage);
  }
  .cover {
    position: absolute;
    left: 256px; top: 50px;
    width: 688px; height: 1100px;
    background: linear-gradient(180deg, var(--cover-top), var(--cover-bottom));
    overflow: hidden;
  }
  .lamp {
    position: absolute;
    left: 144px; top: -50px;
    width: 400px; height: 400px;
  }
  .title {
    position: absolute;
    left: 0; right: 0; top: 420px;
    text-align: center;
    font-family: "Roboto", Arial, sans-serif;
    font-weight: 700;
    color: var(--ink);
  }
  .title__line {
    display: block;
    font-size: 48px;
    line-height: 74px;
    letter-spacing: 0.08em;
  }
  .title__key {
    display: block;
    margin-top: 4px;
    font-family: "Poppins", sans-serif;
    font-size: 76px;
    line-height: 90px;
    letter-spacing: 0.06em;
    color: var(--accent);
  }
  .pillars {
    position: absolute;
    left: 0; right: 0; top: 884px;
    display: flex;
    justify-content: space-between;
    padding: 0 40px;
  }
  .pillar {
    display: flex; flex-direction: column; align-items: center;
  }
  .pillar__icon {
    width: 68px; height: 68px;
    border-radius: 50%;
    background: rgba(42, 38, 34, 0.22);
  }
  .pillar__label {
    margin-top: 22px;
    font-family: "Poppins", sans-serif;
    font-weight: 600;
    font-size: 22px;
    letter-spacing: 0.07em;
    white-space: nowrap;
    color: var(--icon-ink);
  }
  .author-band {
    position: absolute;
    left: 0; right: 0; bottom: 0;
    height: 64px;
    background: var(--band);
    display: flex; align-items: center; justify-content: center;
  }
  .author-band__name {
    font-family: "Poppins", sans-serif;
    font-weight: 600;
    font-size: 25px;
    letter-spacing: 0.08em;
    color: var(--band-text);
  }
</style>
</head>
<body>
  <main class="cover">
    <svg class="lamp" viewBox="0 0 400 400" role="img" aria-label="Glowing light bulb hanging from a cord">
      <circle cx="200" cy="200" r="200" fill="var(--glow-outer)"/>
      <circle cx="200" cy="200" r="128" fill="var(--glow-inner)"/>
    </svg>

    <h1 class="title">
      <span class="title__line">Ways</span>
      <span class="title__line">to Turn</span>
      <span class="title__line">Into</span>
      <span class="title__line">a Bold</span>
      <span class="title__key">Pathfinder</span>
    </h1>

    <section class="pillars">
      <div class="pillar">
        <div class="pillar__icon" role="img" aria-label="Head with light bulb icon"></div>
        <span class="pillar__label">MINDSET</span>
      </div>
      <div class="pillar">
        <div class="pillar__icon" role="img" aria-label="Light bulb with eye icon"></div>
        <span class="pillar__label">INSIGHTS</span>
      </div>
      <div class="pillar">
        <div class="pillar__icon" role="img" aria-label="Gears icon"></div>
        <span class="pillar__label">SKILLS &amp; TOOLS</span>
      </div>
    </section>

    <footer class="author-band">
      <span class="author-band__name">JOOST TER BRAKEL</span>
    </footer>
  </main>
</body>
</html>
```